KR Appraisals website redesign

I would like to refresh my existing website of www.krappraisals-example.com with new graphics, look and feel, as well as updated structure and wording. Content and layout changes have been uploaded to this project Brief.

My existing website has a dark feel. I am now looking for a light and energetic feel. Financial Services is my industry, so the website should be reflect that. I would also like to reflect the concepts of Trust, Service and Expertise.

The website must be serious and upmarket.

Target Market(s)

Corporate board members, CFO's, treasurers and controllers
Auditors, tax advisors, private equity and venture capital asset managers, investors, tax authorities

Industry/Entity Type

Financial Service

Coding

Coded - Design and coding required

Number of Pages Required

5+ page

Font styles to use
Sans Serif
Other font styles liked:
• Designer can choose another modern font

Colors
0355a3
3277b5
85acd3
eaf1f7
f37122
f68d4d
9bcb3c
acd037
cadf82

Requirements
Must have
• Good hi resolution pictures that convey "Finance", "Trust", "Service" or "Expertise".
• An anti-bot (such as Captcha) mechanism in the contact form.
Should not have
• Must not have all content on one rolling screen.

```html
<!DOCTYPE html>
<html lang="en">
<head>
<meta charset="utf-8">
<title>News &amp; Views – KR Appraisals</title>
<link href="https://fonts.googleapis.com/css2?family=Montserrat:wght@500;600&family=Mulish:wght@300;400&display=swap" rel="stylesheet">
<style>
:root{
  --blue:#0355a3;
  --orange:#f37122;
  --green:#9bcb3c;
  --ink:#333333;
  --text:#666666;
  --nav:#6b6b6b;
  --card:#f2f2f2;
  --footer:#333333;
  --footer-text:#9a9a9a;
  --rule:#555555;
}
*{margin:0;padding:0;box-sizing:border-box}
html,body{width:712px;height:1200px;overflow:hidden;background:#fff}
body{position:relative;font-family:"Mulish",sans-serif;font-weight:300;color:var(--text);font-size:7px;line-height:11.55px}
.site-header{position:absolute;left:0;top:0;width:712px;height:60px;background:linear-gradient(90deg,#e6e6dc 0%,#eeeee4 45%,#f4f4e6 100%)}
.brand{position:absolute;left:96px;top:22px;display:flex;align-items:center;gap:5px;font-family:"Montserrat",sans-serif;font-weight:500;font-size:12px;color:#777;letter-spacing:.3px}
.brand .mark{width:9px;height:9px;background:#888}
.main-nav{position:absolute;top:27px;left:0;width:712px;font-family:"Montserrat",sans-serif;font-weight:500;font-size:6.6px;color:var(--nav)}
.main-nav a{position:absolute;color:inherit;text-decoration:none;white-space:nowrap}
.main-nav a.active{color:var(--blue)}
.page-title{position:absolute;top:108px;width:712px;text-align:center;font-family:"Montserrat",sans-serif;font-weight:600;font-size:23px;line-height:28px;color:var(--orange)}
.article{position:absolute;left:96px;top:156px;width:340px}
.article h1{font-family:"Montserrat",sans-serif;font-weight:500;font-size:13.2px;line-height:18px;color:var(--ink)}
.date{color:var(--blue);font-weight:400;font-size:6.6px;line-height:10px}
.article .date{margin-bottom:13px}
.article p{margin-bottom:11.55px}
.article h2{font-family:"Montserrat",sans-serif;font-weight:500;font-size:8.6px;line-height:12px;color:var(--blue);margin-top:7px;margin-bottom:2px}
.values{list-style:none;margin:8px 0 20px}
.values li{position:relative;padding-left:10px;margin-bottom:8px}
.values li::before{content:"";position:absolute;left:0;top:3.5px;width:4px;height:4px;border-radius:50%;background:var(--green)}
.news-card{position:absolute;left:457px;width:160px;height:123px;background:var(--card);padding:11px 5px 0 7px}
.news-card h3{font-family:"Montserrat",sans-serif;font-weight:500;font-size:6.8px;line-height:11.6px;color:var(--ink)}
.news-card .date{margin:1px 0 10px}
.news-card p{font-size:6.7px;line-height:11.5px}
.read-more{display:block;margin-top:3px;font-family:"Montserrat",sans-serif;font-weight:600;font-size:6.8px;color:var(--green);text-decoration:none}
.site-footer{position:absolute;left:0;top:990px;width:712px;height:210px}
.site-footer svg.shape{position:absolute;left:0;top:0}
.footer-brand{position:absolute;top:35px;width:712px;display:flex;justify-content:center;align-items:center;gap:5px;font-family:"Montserrat",sans-serif;font-weight:500;font-size:12px;color:#9a9a9a}
.footer-brand .mark{width:9px;height:9px;background:#9a9a9a}
.footer-nav{position:absolute;left:96px;top:87px;width:521px;height:27px;border-top:1px solid var(--rule);border-bottom:1px solid var(--rule);font-family:"Montserrat",sans-serif;font-weight:500;font-size:6.8px;color:#8a8a8a}
.footer-nav a{position:absolute;top:8px;color:inherit;text-decoration:none;white-space:nowrap}
.footer-nav a.active{color:var(--green)}
.footer-col{position:absolute;top:131px;font-size:6.6px;line-height:13.5px;color:var(--footer-text)}
.footer-col h4{font-family:"Montserrat",sans-serif;font-weight:600;font-size:7.8px;color:var(--orange);margin-bottom:4px}
.footer-col .hl{color:var(--green)}
.footer-col .wh{color:#e6e6e6}
.contact-line{display:flex;gap:5px;align-items:flex-start}
.contact-line svg{flex:none;margin-top:2px}
.addr{line-height:10px}
.phone{margin-top:9px;color:#eee;font-weight:400}
.badge{position:absolute;background:#555}
</style>
</head>
<body>
<header class="site-header">
  <div class="brand"><span class="mark"></span>KR APPRAISALS</div>
  <nav class="main-nav">
    <a style="left:363px">HOME</a>
    <a style="left:407px">ABOUT</a>
    <a style="left:455px">SERVICES</a>
    <a class="active" style="left:511px">NEWS &amp; VIEWS</a>
    <a style="left:584px">CONTACT</a>
  </nav>
</header>

<h2 class="page-title">NEWS &amp; VIEWS</h2>

<article class="article">
  <h1>Dutch GAAP Update – Goodwill and Definitions of Value</h1>
  <div class="date">March 9, 2016</div>
  <p>A number of Dutch GAAP accounting changes took effect on January 1, 2016, some of which affect goodwill and definitions of value. This paper briefly discusses the updates to goodwill and definitions of value and assumes a practitioner’s understanding on basic definitions of value. Please do not hesitate to let us know if you would like further information.</p>
  <h2>Goodwill</h2>
  <p>The recently published 2015 edition of the Dutch GAAP accounting handbook “Richtlijnen voor de jaarverslaggeving voor grote en middelgrote rechtspersonen” includes some key changes affecting goodwill.</p>
  <p>Transaction-related goodwill generated on or after January 1, 2016 must be capitalized and amortized. Goodwill could previously be recorded in three ways: a) write off through the profit and loss statement; b) write off directly against equity; or c) capitalize and subsequently amortize. Starting in January 2016, only one method is allowed – capitalize and amortize. This is one of the areas where Dutch GAAP deviates from IFRS, where goodwill should not be amortized, but rather tested at least annually for impairment.</p>
  <p>Goodwill amortization period has also changed. Previously, goodwill could be amortized up to 5 years unless there was a reasonable basis to apply a longer period. As from January 2016, goodwill may be amortized up to 10 years unless there is a reasonable basis to apply a longer period, but not more than 20 years.</p>
  <h2>Definition of Value</h2>
  <p style="margin-bottom:0">‘Besluit actuele waarde’, the Dutch legislation regulating fair value for accounting purposes, includes a number of changes to definitions of value. Five definitions of value are covered by this legislation – marktwaarde (fair market value), opbrengstwaarde (maximum selling price), bedrijfswaarde (value in use), vervangingswaarde (replacement value) and actuele kostprijs (defined below). A definition of each standard of value according to Dutch law is as follows:</p>
  <ul class="values">
    <li>Marktwaarde (fair market value): the amount for which an asset could be traded or a liability settled between well-informed independent parties who are able to transact.</li>
    <li>pbrengstwaarde (maximum selling price): sometimes referred to as ‘value in exchange’ or ‘fair value less [costs of disposal / costs to sell]’ in other jurisdictions, the maximum amount for which an asset could be sold excluding related transaction costs.</li>
    <li>Bedrijfswaarde (value in use): the monetary value to a company of an asset or group of assets based on the future cash flows that such company could receive by carrying out its business activities.</li>
    <li>Vervangingswaarde (replacement value): the amount that would be required by a company to replace an asset that is used by the company in its business activities with another asset of the same economic characteristics.</li>
    <li>Actuele kostprijs: Either a) the present purchase price and additional costs of the asset, reduced by depreciation (depreciated replacement cost); or b) the costs to purchase the raw materials used for manufacturing the asset, reduced by depreciation (depreciated reproduction cost).</li>
  </ul>
  <p>‘Fair market value’ is no longer allowed for companies where at least 2 of the following conditions apply: 1) assets are less than or equal to €350k; 2) net revenues are less than or equal to €700k; 3) average number of employees over the year are less than 10. Other valuation approaches could be applicable to such companies depending on the purpose of value.</p>
  <p>When tangible or intangible fixed assets are recorded at fair value, the lower of ‘actuele kostprijs’ and ‘value in use’ should be used, with one exception. If ‘maximum selling price’ is lower than ‘actuele kostprijs’ but higher than ‘value in use’, ‘maximum selling price’ should be applied.</p>
  <p>‘Replacement value’ was previously required for assets held for sale. Definition of value has been removed from this legislation for assets held for sale. In an effort to ensure that assets held for sale are not valued too high, the legislation no longer prescribes a definition of value for assets held for sale.</p>
  <p>If you would like more information about Dutch GAAP valuations, please contact Martin Lowe, managing director of KR Appraisals at +31 70 555 0142 or mlowe[@]krappraisals-example.com.</p>
</article>

<aside>
  <div class="news-card" style="top:155px">
    <h3>Martin Lowe to Speak at TradeBridge on Feb 18 in Oosterhout, the Netherlands</h3>
    <div class="date">February 4, 2016</div>
    <p>At $265 billion, the Netherlands is the 3rd largest foreign investor in the United States. The United States is the largest foreign...</p>
    <a class="read-more">READ MORE</a>
  </div>
  <div class="news-card" style="top:297px">
    <h3>KR Appraisals presenteert bij TradeBridge op 18 februari in Oosterhout</h3>
    <div class="date">February 4, 2016</div>
    <p>Leiden, 2 februari 2016 – Martin Lowe, managing director van KR Appraisals, presenteert bij TradeBridge op 18 februari in...</p>
    <a class="read-more">READ MORE</a>
  </div>
  <div class="news-card" style="top:438px">
    <h3>Veldhaven University Extends Financial Training Contract with KR Appraisals</h3>
    <div class="date">September 7, 2015</div>
    <p>eiden, The Netherlands, September 7, 2015 – Veldhaven University has extended its contract with the financial training brand of...</p>
    <a class="read-more">READ MORE</a>
  </div>
</aside>

<footer class="site-footer">
  <svg class="shape" width="712" height="210" viewBox="0 0 712 210"><polygon points="0,40 356,0 712,40 712,210 0,210" fill="var(--footer)"/></svg>
  <div class="footer-brand"><span class="mark"></span>KR APPRAISALS</div>
  <nav class="footer-nav">
    <a class="active" style="left:133px">HOME</a>
    <a style="left:178px">ABOUT</a>
    <a style="left:225px">SERVICES</a>
    <a style="left:281px">NEWS &amp; VIEWS</a>
    <a style="left:354px">CONTACT</a>
  </nav>
  <div class="footer-col" style="left:97px">
    <h4>CREDITS</h4>
    <div>© 2019 <span class="hl">KR Appraisals</span></div>
    <div>Logo by <span class="wh">Lotte Brinkman</span></div>
    <div>Website by <span class="hl">Clearline Studio</span></div>
  </div>
  <div class="footer-col" style="left:231px">
    <h4>LEIDEN</h4>
    <div class="contact-line"><svg width="6" height="8" viewBox="0 0 6 8"><path d="M3 0a3 3 0 0 0-3 3c0 2.2 3 5 3 5s3-2.8 3-5a3 3 0 0 0-3-3zm0 4.2a1.2 1.2 0 1 1 0-2.4 1.2 1.2 0 0 1 0 2.4z" fill="var(--green)"/></svg><div class="addr">Kanaalweg 48<br>2300 AB Leiden</div></div>
    <div class="contact-line phone"><svg width="8" height="8" viewBox="0 0 8 8"><path d="M1.6.3l1.2 1.5-.7 1.1c.5 1 1.4 1.9 2.4 2.4l1.1-.7 1.5 1.2-.6 1.5C3.6 7.1.9 4.4.1.9z" fill="var(--green)"/></svg>070 555 0142</div>
  </div>
  <div class="footer-col" style="left:366px">
    <h4>AMSTERDAM</h4>
    <div class="contact-line"><svg width="6" height="8" viewBox="0 0 6 8"><path d="M3 0a3 3 0 0 0-3 3c0 2.2 3 5 3 5s3-2.8 3-5a3 3 0 0 0-3-3zm0 4.2a1.2 1.2 0 1 1 0-2.4 1.2 1.2 0 0 1 0 2.4z" fill="var(--green)"/></svg><div class="addr">Zuidplein 15<br>1070 XY Amsterdam</div></div>
    <div class="contact-line phone"><svg width="8" height="8" viewBox="0 0 8 8"><path d="M1.6.3l1.2 1.5-.7 1.1c.5 1 1.4 1.9 2.4 2.4l1.1-.7 1.5 1.2-.6 1.5C3.6 7.1.9 4.4.1.9z" fill="var(--green)"/></svg>020 555 0187</div>
  </div>
  <div class="badge" role="img" aria-label="Partner certification badge" style="left:508px;top:125px;width:102px;height:22px;border-radius:3px"></div>
  <div class="badge" role="img" aria-label="Professional membership badge" style="left:507px;top:154px;width:100px;height:30px;border-radius:3px"></div>
</footer>
</body>
</html>
```